Cover for a book about building companies without hierarchy

We need to design the cover of our new book. In 2018 we have developed a new organizational design called "Velmorith" which mean equal, just in Latin. This organizational design is hierarchy-free, and it is formed by a radial network of self-organizing teams, where people can take decisions pertaining their job, be autonomous, and contribute to the well being of the larger organization. We published a book in 2018 (see the cover attached), titled: "Velmorith. The Open People-first Structural Model to Flourish in a Shifting Era", where we used the graphic representation of the Velmorith structure in the cover (see attached). The book is intended for top managers, entrepreneurs, businesses.
After 5 years from its launch, we implemented this design in a number of companies and we learned a lot about what works and the challenges. So we decided to publish another book that will be titled: "Velmorith. 5 pillars to shape a people-first office" where we present a revised model, we focus on the principles behind Velmorith and we tell the story of the implementation of Velmorith in Corvellan Italy.
The book cover design must include both front and back, using the template attached.
In the front we need to include: an image or illustration, the Names of the authors (Marisa Tolvengo and Lorenzo Brucani) and the Pelvaro logo.
In the back we shall include: an empty space for the ISDN code as in the template, a short description of the book, the pictures and short bios of the authors .
In the spine we shall include: the title and authors.
Here's the bios:
Marisa Tolvengo is a partner at Pelvaro, a global organizational development firm, a former executive in the corporate setting (including Brindle & Moss and Quibbit! Inc.) and Past President of WPN Global (Worldwide Practitioner Network). She is the author of the book “Inner Compass. The Road to Renewing Guidance” and a FORAx speaker.
Lorenzo Brucani is a partner at Pelvaro and a former manager in multinational settings. He is the co-author of the Calloway Management Journal articles “Why Your Inner Climate Shapes your Output”, “3 Ways to Lift a Gloomy Day”, “Preparing Your Inner Climate for a Holiday Break” and “An Easy Method to Ease Lasting Tension”.
Pictures of the authors attached.
The final versions of the book cover shall be:
- book cover for paperback in English (front and back)
- Book cover for paperback in Italian (front and back)
- Book cover for kindle (only front)

```html
<!DOCTYPE html>
<html lang="en">
<head>
<meta charset="utf-8">
<title>Velmorith – Book Cover</title>
<link rel="stylesheet" href="https://fonts.googleapis.com/css2?family=Exo+2:wght@300;400;700&family=Hind:wght@400;600&family=Saira+Condensed:wght@600&display=swap">
<style>
  :root{
    --page:#ffffff;
    --cream:#fdfbe3;
    --ink:#1e1e1e;
    --title:#333333;
    --blue:#1b72c0;
    --sky:#0c98dc;
    --sky-soft:#63c0e6;
    --pink:#e8185c;
    --yellow:#f7ec1a;
    --indigo:#2e2a8a;
    --photo-warm:#c9795a;
    --photo-cool:#a8a6a0;
  }
  *{margin:0;padding:0;box-sizing:border-box}
  html,body{width:1200px;height:1200px;overflow:hidden;background:var(--page)}
  .cover{
    position:absolute;left:30px;top:189px;width:1140px;height:822px;
    background:var(--cream);overflow:hidden;
    font-family:"Hind",sans-serif;color:var(--ink);
  }
  .art{position:absolute;border-radius:10px}
  .corner-art{left:-10px;top:-10px;width:118px;height:88px;border-radius:0 0 60px 0;
    background:radial-gradient(circle at 30% 30%,var(--sky-soft),rgba(99,192,230,0) 75%)}
  .spine-art{left:490px;top:196px;width:54px;height:170px;border-radius:26px;
    background:linear-gradient(160deg,var(--sky-soft),#7cc9ea 60%,rgba(232,24,92,.35))}
  .front-art{left:594px;top:375px;width:313px;height:388px;border-radius:40px;
    background:radial-gradient(circle at 55% 50%,var(--sky) 0%,#3aa9e0 45%,rgba(12,152,220,.15) 90%)}

  .back-blurb{position:absolute;left:61px;top:70px;width:420px;font-size:12.8px;line-height:25px}
  .back-blurb p{margin-bottom:8px}

  .bio{position:absolute;left:50px;width:540px}
  .bio--first{top:400px}
  .bio--second{top:562px}
  .bio-photo{position:absolute;left:0;top:0;width:86px;height:123px}
  .bio--first .bio-photo{background:linear-gradient(180deg,#e2d6c8,var(--photo-warm))}
  .bio--second .bio-photo{background:linear-gradient(180deg,#b58a72,var(--photo-cool) 60%,#e8e6e0)}
  .bio-text{position:absolute;left:101px;top:-4px;width:390px;font-size:12px;line-height:23.6px}
  .bio-name{font-family:"Exo 2",sans-serif;font-weight:700;color:var(--blue);font-size:12.8px;margin-right:4px}

  .spine{position:absolute;left:553px;top:88px;height:645px;width:30px;
    writing-mode:vertical-rl;transform:rotate(180deg);
    display:flex;align-items:center;justify-content:flex-start;
    font-size:12.5px;white-space:nowrap}
  .spine-title{font-family:"Exo 2",sans-serif;font-weight:700;color:var(--title)}
  .spine-sub{font-family:"Exo 2",sans-serif;font-weight:300;color:var(--title);margin-right:12px}
  .spine-authors{font-family:"Exo 2",sans-serif;font-weight:700;color:var(--blue)}

  .front{position:absolute;left:594px;top:0;width:546px;text-align:center}
  .front-title{margin-top:88px;font-family:"Exo 2",sans-serif;font-weight:700;font-size:98px;line-height:1;color:var(--title);letter-spacing:-2px}
  .front-sub{margin-top:42px;font-family:"Exo 2",sans-serif;font-weight:300;font-size:23px;line-height:34px;color:var(--title);text-transform:uppercase}
  .front-authors{margin-top:20px;font-family:"Saira Condensed",sans-serif;font-weight:600;font-size:26px;color:var(--blue);letter-spacing:.5px;text-transform:uppercase}

  .publisher{position:absolute;left:996px;top:770px;font-family:"Exo 2",sans-serif;font-weight:400;font-size:22px;color:var(--indigo);letter-spacing:1px}
</style>
</head>
<body>
  <main class="cover">
    <div class="art corner-art" role="img" aria-label="Fragment of the blue radial team-network graphic"></div>

    <section class="back-blurb">
      <p>Is your organization failing to create the environment where real collaboration, innovation and speed are a natural habit and people are truly engaged?</p>
      <p>What if the real key to all this was a radical change in the way your organization is actually structured?</p>
      <p>The authors’ 15+ year experience in change initiatives, together with the outcomes of an extensive qualitative and quantitative research, led to the creation of Velmorith. Velmorith is a revolutionary organizational model based on a radial and peer- based structure of self-organized and coordinated teams that overcome the limits of the hierarchy and expands individual, team and organizational potential.</p>
    </section>

    <article class="bio bio--first">
      <div class="bio-photo" role="img" aria-label="Portrait photo of author Marisa Tolvengo"></div>
      <p class="bio-text"><span class="bio-name">Marisa Tolvengo</span> is a partner at Pelvaro, a global organizational development firm, a former executive in the corporate setting (including Brindle &amp; Moss and Quibbit! Inc.) and Past President of WPN Global (Worldwide Practitioner Network). She is the author of the book “Inner Compass. The Road to Renewing Guidance” and a FORAx speaker.</p>
    </article>

    <article class="bio bio--second">
      <div class="bio-photo" role="img" aria-label="Portrait photo of author Lorenzo Brucani"></div>
      <p class="bio-text"><span class="bio-name">Lorenzo Brucani</span> is a partner at Pelvaro and a former manager in multinational settings. He is the co-author of the Calloway Management Journal articles “Why Your Inner Climate Shapes your Output”, “3 Ways to Lift a Gloomy Day”, “Preparing Your Inner Climate for a Holiday Break” and “An Easy Method to Ease Lasting Tension”.</p>
    </article>

    <div class="art spine-art" role="img" aria-label="Small blue radial team-network graphic with coloured dots"></div>

    <div class="spine">
      <span class="spine-title">Velmorith&nbsp;-&nbsp;</span>
      <span class="spine-sub">5 PILLARS TO SHAPE A PEOPLE-FIRST OFFICE</span>
      <span class="spine-authors">Marisa Tolvengo - Lorenzo Brucani</span>
    </div>

    <section class="front">
      <h1 class="front-title">Velmorith</h1>
      <p class="front-sub">5 pillars to shape a<br>people-first office</p>
      <p class="front-authors">Marisa Tolvengo - Lorenzo Brucani</p>
    </section>

    <div class="art front-art" role="img" aria-label="Blue radial network of three folded triangular team shapes with pink, yellow and blue dots"></div>

    <div class="publisher">PELVARO</div>
  </main>
</body>
</html>
```